"Fight Back" banner ad design

We have sketched the design and have images to consider including. We are looking for something striking, FIGHT BACK! with a clenched fist image, then a fading images of variance.png and hi-bill.png in the background. Tag line "Fight your water bill with your own data" optionally include "Tally Mode" rivo3196 logo, KPMT Design, LLC based in San Diego CA. Pre-order now, visit https://www.fundbeacon.com/rivometer @rivo3196, info@rivo3196.com

"Fight your water bill with your own data"

```html
<!DOCTYPE html>
<html lang="en">
<head>
<meta charset="utf-8">
<title>Fight Your Water Bill – Tally Mode</title>
<link rel="stylesheet" href="https://fonts.googleapis.com/css2?family=Arimo:ital,wght@0,400;0,700;1,700&display=swap">
<style>
:root{
  --ray-light:#f4f9fd;
  --ray-blue:#a9cdea;
  --chevron:#3d86c6;
  --chevron-edge:#bfe4f7;
  --teal-dark:#1d5a6c;
  --teal-light:#4f8f9f;
  --drop-white:#ffffff;
  --drop-blue:#b9d3e3;
  --skin:#c79071;
  --skin-dark:#8f5a3e;
  --table-head:#1f5e6e;
  --table-foot:#8fd0e0;
  --ink:#111;
  --brand:#3c8797;
  --panel-top:#5a5a5a;
  --panel-bottom:#3e3e3e;
  --panel-bar:#d6d6d6;
  --yellow:#eef27a;
  --cyan-text:#c9f1f8;
  --white:#fff;
}
*{box-sizing:border-box;margin:0;padding:0}
html,body{width:1200px;height:900px;overflow:hidden;background:#fff}
body{font-family:"Arimo",Arial,sans-serif;position:relative}
.backdrop{position:absolute;inset:0}
.fist-photo{position:absolute;left:70px;top:480px;width:225px;height:420px;
  background:radial-gradient(ellipse at 45% 25%,var(--skin) 0%,#b07a5c 45%,var(--skin-dark) 100%);
  border-radius:90px 90px 20px 20px;opacity:.9}
.brand{position:absolute;left:458px;top:268px;display:flex;flex-direction:column;align-items:center;gap:18px}
.brand-dot{width:52px;height:52px;border-radius:50%;background:var(--brand)}
.brand-name{font-weight:700;font-size:26px;color:var(--brand);letter-spacing:.5px}

.fees{position:absolute;left:750px;top:16px;width:433px;height:408px;background:#fff;
  border:2px solid var(--table-head);font-size:15px;color:var(--ink);display:flex;flex-direction:column}
.fees-title{background:var(--table-head);color:var(--white);font-weight:700;text-align:center;font-size:17px;height:21px;line-height:21px}
.fees-body{flex:1;padding:8px 12px 0 4px}
.row{display:grid;grid-template-columns:1fr 70px;height:18.5px;line-height:18.5px}
.row .amt{text-align:right}
.section{font-weight:700}
.i1{padding-left:13px}
.tier{display:grid;grid-template-columns:82px 48px 36px 18px 66px 1fr;height:18.5px;line-height:18.5px;padding-left:26px}
.tier .n{text-align:right;padding-right:6px}
.tier .amt{text-align:right}
.rate-line{display:grid;grid-template-columns:1fr 170px;height:18.5px;line-height:18.5px}
.rate-line span:last-child{border-bottom:1px solid var(--ink);padding-left:6px}
.gap{height:18px}
.gap-lg{height:36px}
.bold{font-weight:700}
.fees-total{background:var(--table-foot);border-top:2px solid var(--table-head);display:grid;grid-template-columns:1fr auto;
  padding:0 12px 0 4px;height:23px;line-height:21px;font-weight:700;font-size:17px}

.headline{position:absolute;left:408px;top:478px;color:var(--white);font-weight:700;font-style:italic;font-size:52px;line-height:56px;
  text-shadow:2px 2px 4px rgba(0,0,0,.35)}
.maker{position:absolute;left:290px;top:733px;width:500px;text-align:center;color:var(--cyan-text);font-weight:700;font-size:30px;line-height:37px;
  text-shadow:1px 1px 3px rgba(0,0,0,.3)}

.promo{position:absolute;left:750px;top:469px;width:428px;height:408px;
  background:linear-gradient(180deg,var(--panel-top),var(--panel-bottom));box-shadow:0 2px 8px rgba(0,0,0,.4)}
.promo-bar{height:21px;background:linear-gradient(180deg,#eee,var(--panel-bar) 60%,#a9a9a9)}
.promo-mode{text-align:center;color:var(--white);font-weight:700;font-size:84px;line-height:86px;margin-top:18px;
  -webkit-text-stroke:1.5px #555;text-shadow:0 0 6px rgba(0,0,0,.6),3px 4px 3px rgba(0,0,0,.5)}
.promo-call{text-align:center;color:var(--yellow);font-weight:700;font-size:29px;line-height:34px;margin-top:30px}
.promo-link{text-align:center;color:var(--ink);font-size:15px;margin-top:18px;text-shadow:0 0 3px #ddd,0 0 2px #fff}
.promo-mail{text-align:center;color:var(--white);font-weight:700;font-size:19px;margin-top:16px}
</style>
</head>
<body>
<svg class="backdrop" width="1200" height="900" viewBox="0 0 1200 900" aria-hidden="false">
  <defs>
    <radialGradient id="raysFill" cx="0.3" cy="0.55" r="0.9">
      <stop offset="0" stop-color="var(--ray-light)"/>
      <stop offset="0.6" stop-color="#d7e9f6"/>
      <stop offset="1" stop-color="var(--ray-blue)"/>
    </radialGradient>
    <radialGradient id="dropsFill" cx="0.5" cy="0.1" r="1">
      <stop offset="0" stop-color="var(--drop-blue)"/>
      <stop offset="0.7" stop-color="#e6f0f6"/>
      <stop offset="1" stop-color="var(--drop-white)"/>
    </radialGradient>
    <linearGradient id="tealFill" x1="0" y1="0" x2="1" y2="1">
      <stop offset="0" stop-color="var(--teal-dark)"/>
      <stop offset="1" stop-color="var(--teal-light)"/>
    </linearGradient>
  </defs>
  <polygon points="0,0 240,0 300,445 240,900 0,900" fill="url(#raysFill)" role="img" aria-label="Pale blue sunburst rays radiating behind the fist"/>
  <polygon points="275,0 1200,0 1200,445 335,445" fill="url(#dropsFill)" role="img" aria-label="Water droplets on a pale blue surface"/>
  <polygon points="335,445 1200,445 1200,900 275,900" fill="url(#tealFill)"/>
  <polygon points="240,0 275,0 335,445 275,900 240,900 300,445" fill="var(--chevron)"/>
  <polyline points="240,0 300,445 240,900" fill="none" stroke="var(--chevron-edge)" stroke-width="5"/>
</svg>

<div class="fist-photo" role="img" aria-label="Raised clenched fist"></div>

<div class="brand">
  <span class="brand-dot"></span>
  <span class="brand-name">Rivo3196</span>
</div>

<section class="fees">
  <div class="fees-title">FEES &amp; CHARGES</div>
  <div class="fees-body">
    <div class="row section"><span>Water Services</span><span></span></div>
    <div class="row i1"><span>Single Family Residential Base Fee</span><span class="amt">48.44</span></div>
    <div class="tier" style="padding-left:13px;grid-template-columns:95px 48px 36px"><span>Water Used</span><span class="n">65</span><span>HCF</span></div>
    <div class="tier"><span>Tier 1</span><span class="n">8.00</span><span>HCF</span><span>@</span><span>$4.8425</span><span class="amt">38.74</span></div>
    <div class="tier"><span>Tier 2</span><span class="n">16.00</span><span>HCF</span><span>@</span><span>$5.4231</span><span class="amt">86.77</span></div>
    <div class="tier"><span>Tier 3</span><span class="n">12.00</span><span>HCF</span><span>@</span><span>$7.7483</span><span class="amt">92.98</span></div>
    <div class="tier"><span>Tier 4</span><span class="n">29.00</span><span>HCF</span><span>@</span><span></span><span class="amt">315.96</span></div>
    <div class="rate-line"><span></span><span>$10.8952</span></div>
    <div class="row i1"><span>Total Charge for Water Used</span><span class="amt">534.45</span></div>
    <div class="gap"></div>
    <div class="row section"><span>Sewer &amp; Storm Drain Services</span><span></span></div>
    <div class="row i1"><span>Sewer Base Fee</span><span class="amt">30.66</span></div>
    <div class="row i1"><span>Sewer Service Charge</span><span class="amt">60.17</span></div>
    <div class="row i1"><span>Storm Drain</span><span class="amt">1.90</span></div>
    <div class="gap-lg"></div>
    <div class="row bold"><span>Total Current Charges</span><span class="amt" style="font-weight:400">675.62</span></div>
    <div class="row"><span>Deferred Due</span><span class="amt">79.66</span></div>
  </div>
  <div class="fees-total"><span>TOTAL DUE</span><span>755.28</span></div>
</section>

<h1 class="headline">Fight Your<br>Water Bill<br>With your<br>Own Data</h1>

<p class="maker">KPMT Design,<br>LLC based in San Diego,<br>CA</p>

<section class="promo">
  <div class="promo-bar"></div>
  <h2 class="promo-mode">TALLY<br>MODE</h2>
  <p class="promo-call">Pre-Order Now,<br>visit:</p>
  <p class="promo-link">Https://www.Fundbeacon.com/rivometer @rivo3196</p>
  <p class="promo-mail">Info@rivo3196.com</p>
</section>
</body>
</html>
```